Local Roofing/Construction company business needs new biz card design

We need a new business card design, current cards are from the start of this operation and generic at best. We are a local Construction Company (General Contractor) with a majority of our work originating from insurance claims-exterior finish work is the main focus (Roofs-Siding-Gutters etc). Heavily involved with homeowners and the low ball offers they receive from insurance company's after a insurable event takes place. I have attached some of our original logo file(s) below.

```html
<!DOCTYPE html>
<html lang="en">
<head>
<meta charset="utf-8">
<title>Stonefield Builders – Business Card</title>
<link rel="stylesheet" href="https://fonts.googleapis.com/css2?family=Montserrat:wght@400;500;700&display=swap">
<style>
  :root {
    --bg: #e4e4e4;
    --green-light: #8ed3a0;
    --green: #5bbb74;
    --green-deep: #4fac68;
    --ink: #0f1c1e;
    --white: #ffffff;
    --soft-white: #f1f1ee;
  }
  * { box-sizing: border-box; margin: 0; padding: 0; }
  html, body {
    width: 1200px; height: 1200px; overflow: hidden;
    background: var(--bg);
    font-family: "Montserrat", sans-serif;
  }
  .sheet {
    position: relative; width: 1200px; height: 1200px;
  }
  .card {
    position: absolute; left: 160px;
    width: 880px; height: 503px;
    border-radius: 28px;
    overflow: hidden;
    box-shadow: 0 6px 18px rgba(0,0,0,0.18);
  }
  .card--front {
    top: 50px;
    background: linear-gradient(90deg, var(--green-light) 0%, var(--green) 55%, var(--green) 100%);
  }
  .card--back {
    top: 597px;
    background: linear-gradient(90deg, #7fc690 0%, var(--green-deep) 50%, var(--green-deep) 100%);
  }

  /* Front: wordmark */
  .front-mark {
    position: absolute; left: 50%; top: 50%;
    transform: translate(-50%, -50%);
    display: flex; flex-direction: column; align-items: center; gap: 22px;
  }
  .front-mark__square {
    width: 150px; height: 150px;
    background: var(--white);
    border-radius: 18px;
  }
  .front-mark__name {
    color: var(--white);
    font-weight: 700;
    font-size: 40px;
    letter-spacing: 2px;
    text-transform: uppercase;
    text-align: center;
    line-height: 1.1;
  }

  /* Back: header badge */
  .badge {
    position: absolute; right: 48px; top: 46px;
    display: flex; align-items: center; gap: 16px;
    background: var(--ink);
    border-radius: 14px;
    padding: 18px 28px;
  }
  .badge__square {
    width: 34px; height: 34px;
    background: var(--green);
  }
  .badge__name {
    color: var(--soft-white);
    font-weight: 700;
    font-size: 28px;
    letter-spacing: 1.5px;
    text-transform: uppercase;
  }

  /* Back: contact block */
  .person {
    position: absolute; left: 90px; bottom: 52px;
    color: var(--soft-white);
  }
  .person__name {
    font-weight: 700; font-size: 34px; letter-spacing: 0.5px;
  }
  .person__role {
    font-weight: 400; font-size: 21px; margin: 4px 0 16px 10px; letter-spacing: 0.5px;
  }
  .contact-list { list-style: none; margin-left: 16px; }
  .contact-list li {
    display: flex; align-items: center; gap: 14px;
    font-size: 22px; font-weight: 400; line-height: 1.55; letter-spacing: 0.3px;
  }
  .contact-list svg { width: 20px; height: 20px; flex: none; }

  .address {
    position: absolute; right: 64px; bottom: 120px;
    color: var(--soft-white);
    text-align: right;
    font-size: 22px; line-height: 1.45; letter-spacing: 0.5px;
  }
</style>
</head>
<body>
<main class="sheet">
  <section class="card card--front" aria-label="Card front">
    <div class="front-mark">
      <div class="front-mark__square"></div>
      <p class="front-mark__name">Stonefield<br>Builders</p>
    </div>
  </section>

  <section class="card card--back" aria-label="Card back">
    <div class="badge">
      <div class="badge__square"></div>
      <p class="badge__name">Stonefield Builders</p>
    </div>

    <div class="person">
      <h1 class="person__name">Marcus Dale</h1>
      <p class="person__role">Founder &amp; Director</p>
      <ul class="contact-list">
        <li>
          <svg viewBox="0 0 24 24" aria-hidden="true"><path fill="#f1f1ee" d="M6.6 10.8a15.1 15.1 0 0 0 6.6 6.6l2.2-2.2c.3-.3.7-.4 1-.2 1.1.4 2.3.6 3.6.6.6 0 1 .4 1 1V20c0 .6-.4 1-1 1A17 17 0 0 1 3 4c0-.6.4-1 1-1h3.5c.6 0 1 .4 1 1 0 1.3.2 2.5.6 3.6.1.3 0 .7-.2 1z"/></svg>
          (555)-014-2290
        </li>
        <li>
          <svg viewBox="0 0 24 24" aria-hidden="true"><path fill="#f1f1ee" d="M2 5h20v14H2z"/><path fill="none" stroke="#4fac68" stroke-width="1.8" d="M2.5 5.5 12 13l9.5-7.5"/></svg>
          info@stonefieldbuilders.com
        </li>
        <li>
          <svg viewBox="0 0 24 24" aria-hidden="true"><circle cx="12" cy="12" r="10" fill="#f1f1ee"/><path fill="none" stroke="#4fac68" stroke-width="1.5" d="M2 12h20M12 2c3 3 3 17 0 20M12 2c-3 3-3 17 0 20"/></svg>
          www.stonefieldbuilders.com
        </li>
      </ul>
    </div>

    <address class="address" style="font-style:normal">
      4870 Alder Lane<br>
      Brookhaven Ohio 40215
    </address>
  </section>
</main>
</body>
</html>
```